Podiatry clinic requires a modern revamp and editing of existing website.

I would like a fresh new look and updated information for my current business website. An easy to navigate site with prominent address and phone number for call to action. We are a podiatry clinic that focuses on general and sports podiatry.
I would like 4 pages; including Home page, About Us, Services & Contact.
www.brambleridgepodiatry.net

Target Market(s)

Active working professionals.

Industry/Entity Type

Medical

Coding

Coded - Design and coding required

Number of Pages Required

4 page

Font styles to use
Sans Serif

Colors
6b449b

Requirements
Must have
• A modern look with logo and active images; clean and uncluttered. Visible phone number and address for call to action.
• 4 pages - Home, About Us, Services, Contact.
• Home page - update address & service logos.
• About Us - update of personal information.
• Services - Revamp of existing page.
• Contact page to include Google map, email & phone number.
Nice to have
• Ability to add content easily; eg. a blog or adding video onto Home page.
• Link to Facebook page.

```html
<!DOCTYPE html>
<html lang="en">
<head>
<meta charset="utf-8">
<title>Bramble Ridge Podiatry</title>
<link rel="stylesheet" href="https://fonts.googleapis.com/css2?family=Open+Sans:wght@400;600;700&family=Raleway:wght@300;400&family=Merriweather:wght@700&display=swap">
<style>
:root{
  --lavender:#9d8bc7;
  --purple:#6b449b;
  --deep:#4a3580;
  --ink:#333;
  --muted:#555;
  --grey-band:#f5f5f5;
  --dark-bar:#3a3a3a;
  --orange:#f05a1e;
  --white:#fff;
}
*{box-sizing:border-box;margin:0;padding:0}
html,body{width:759px;height:1200px;overflow:hidden}
body{position:relative;background:var(--white);font-family:"Open Sans",sans-serif;color:var(--ink)}
.abs{position:absolute}

.site-header{left:0;top:0;width:759px;height:75px;background:var(--lavender)}
.brand{left:68px;top:14px;display:flex;align-items:center;gap:6px;color:var(--white);font-weight:700;font-size:12px;line-height:1.15;width:110px}
.brand-dot{width:14px;height:14px;border-radius:50%;background:var(--purple);flex:none}
.book-btn{left:429px;top:9px;width:128px;height:22px;background:var(--deep);color:var(--white);font-size:9.5px;display:flex;align-items:center;justify-content:center;gap:6px}
.call{left:582px;top:7px;color:var(--ink);display:flex;gap:6px;align-items:center}
.call small{display:block;font-size:8.5px}
.call strong{display:block;font-size:13px;font-weight:400}
.main-nav{left:427px;top:48px;display:flex;gap:29px;font-size:10.5px;color:var(--white)}
.main-nav .active{color:var(--deep);font-weight:600}

.hero{left:0;top:75px;width:759px;height:240px;background:linear-gradient(180deg,#e9c77c 0%,#d8b46a 45%,#8a7a55 80%,#5a5040 100%)}
.hero h1{left:62px;top:76px;width:270px;font-family:"Merriweather",serif;font-size:16px;line-height:27px;color:#1d1d1d}
.arrow-btn{top:118px;width:20px;height:18px;background:#2f2f2f;display:flex;align-items:center;justify-content:center}

.tile{top:345px;width:195px;height:126px;display:flex;align-items:flex-end;justify-content:center;padding-bottom:10px;color:var(--white);font-size:18px;font-weight:600;text-shadow:0 1px 3px rgba(0,0,0,.5)}
.side-figure{top:480px;width:130px;height:330px;background:linear-gradient(180deg,rgba(180,180,200,.15),rgba(200,200,210,.05))}

.welcome{left:0;top:516px;width:759px;text-align:center;font-family:"Raleway",sans-serif;font-weight:300;font-size:21px;color:var(--deep)}
.rule{left:300px;top:545px;width:160px;height:1px;background:#bbb}
.intro{left:82px;top:557px;width:575px;text-align:center;font-size:9px;line-height:16px;color:var(--muted)}
.video{left:266px;top:640px;width:212px;height:142px;background:linear-gradient(135deg,#e9eef2,#c9d2d8 60%,#b7a99b);border:1px solid #555}
.video-bar{left:0;bottom:0;width:100%;height:18px;background:#222}
.enquiry{left:0;top:801px;width:759px;text-align:center;font-size:12.5px;color:var(--ink)}
.enquiry b{font-weight:600}

.affiliations{left:0;top:853px;width:740px;height:127px;background:var(--grey-band)}
.affiliations h2{left:0;top:17px;width:700px;text-align:center;font-family:"Raleway",sans-serif;font-weight:400;font-size:20px;color:var(--deep)}
.badge{top:62px;width:123px;height:47px;background:var(--white);border:1px solid #ccc;display:flex;align-items:center;justify-content:center}
.badge span{width:95px;height:30px;background:#dfe3ea}

.eligibility{left:0;top:979px;width:759px;height:51px;background:var(--dark-bar)}
.eligibility p{left:65px;top:8px;width:470px;color:var(--white);font-size:12px;line-height:16px}
.book-orange{left:545px;top:11px;width:131px;height:22px;background:var(--orange);color:var(--white);font-size:9.5px;display:flex;align-items:center;justify-content:center;gap:5px}

.footer h3{top:1043px;font-size:11.5px;font-weight:400;color:var(--ink);padding-bottom:5px;border-bottom:1px dotted #bbb;white-space:nowrap}
.quick-links{left:62px;top:1071px;list-style:none;font-size:8px;line-height:14.8px;color:var(--ink)}
.quick-links li::before{content:"›";color:#aaa;margin-right:7px}
.contact-list{left:205px;top:1069px;width:150px;font-size:8px;line-height:11px}
.contact-item{display:flex;gap:6px;padding-bottom:9px;margin-bottom:9px;border-bottom:1px solid #e3e3e3}
.contact-item:last-child{border:none}
.hours{left:426px;top:1071px;width:102px;font-size:8px;line-height:11px}
.hours div{padding-bottom:6px;margin-bottom:6px;border-bottom:1px solid #e3e3e3}
.hours div:last-child{border:none}
.col-divider{top:1050px;width:1px;height:115px;background:#e6e6e6}
.footer-logo{left:587px;top:1055px;width:100px;height:88px;background:var(--lavender);display:flex;align-items:center;justify-content:center;gap:5px;color:var(--white);font-weight:700;font-size:11px;line-height:1.2;padding:0 8px}

.bottom-bar{left:0;top:1174px;width:759px;height:26px;background:var(--lavender)}
.bottom-bar p{left:62px;top:7px;font-size:8px;color:var(--white)}
.social{top:4px;width:19px;height:19px;border-radius:50%;background:#cfc6e4}
</style>
</head>
<body>

<header class="site-header abs">
  <div class="brand abs"><span class="brand-dot"></span>Bramble Ridge Podiatry</div>
  <div class="book-btn abs">
    <svg width="12" height="12" viewBox="0 0 12 12" fill="none" stroke="#fff" stroke-width="1"><rect x="1" y="2" width="9" height="9"/><line x1="1" y1="4.5" x2="10" y2="4.5"/></svg>
    Book An Appointment
  </div>
  <div class="call abs">
    <svg width="17" height="17" viewBox="0 0 17 17" fill="none" stroke="#222" stroke-width="1.2"><circle cx="8.5" cy="8.5" r="7.5"/><path d="M6 5c0 4 2 6 5 7"/></svg>
    <div><small>Call Us Today</small><strong>1300 482 907</strong></div>
  </div>
  <nav class="main-nav abs">
    <span class="active">Home</span><span>About Us</span><span>Services</span><span>Contact Us</span>
  </nav>
</header>

<section class="hero abs" role="img" aria-label="Runner's legs mid-stride on a grassy hilltop at sunrise">
  <h1 class="abs">Bramble Ridge Podiatry Is A Podiatry Clinic In The Heart Of Melbourne CBD</h1>
  <div class="arrow-btn abs" style="left:0"><svg width="6" height="9" viewBox="0 0 6 9"><path d="M5 1L1 4.5 5 8" stroke="#fff" stroke-width="1.5" fill="none"/></svg></div>
  <div class="arrow-btn abs" style="left:732px"><svg width="6" height="9" viewBox="0 0 6 9"><path d="M1 1l4 3.5L1 8" stroke="#fff" stroke-width="1.5" fill="none"/></svg></div>
</section>

<div class="side-figure abs" style="left:0" role="img" aria-label="Faint photo of a smiling woman in sportswear"></div>
<div class="side-figure abs" style="left:629px" role="img" aria-label="Faint photo of a baseball pitcher"></div>

<div class="tile abs" style="left:69px;background:linear-gradient(160deg,#c9c3bb,#8f8478)" role="img" aria-label="Basketball player holding an injured ankle">Sports Injuries</div>
<div class="tile abs" style="left:282px;background:linear-gradient(160deg,#d9dde0,#9e9a93)" role="img" aria-label="Hands fitting an orthotic insole">Orthotic Therapy</div>
<div class="tile abs" style="left:493px;background:linear-gradient(160deg,#7aa5c6,#e2d3c4)" role="img" aria-label="Gloved hands treating a toenail">Nail Surgery</div>

<h2 class="welcome abs">Welcome to Bramble Ridge Podiatry</h2>
<div class="rule abs"></div>
<p class="intro abs">Bramble Ridge Podiatry is a Podiatry clinic in the heart of Melbourne CBD. We are located between Larkfield &amp; Denholm Streets in the Harbourline Business Centre / Linden Hotel Complex. Our podiatrists are fully qualified health professionals who are able to diagnose, treat, manage or help to prevent all medical conditions that affect the feet and lower limb. We provide General Podiatry Treatment and some Specialised Services in relation to various foot conditions, including Sports Injuries, Orthotic Therapy and Nail Surgery.</p>

<div class="video abs" role="img" aria-label="Video still of a podiatrist examining a patient's foot">
  <svg class="abs" style="left:102px;top:58px" width="32" height="22" viewBox="0 0 32 22"><rect width="32" height="22" rx="4" fill="#111"/><path d="M13 6l7 5-7 5z" fill="#fff"/></svg>
  <div class="video-bar abs">
    <svg width="212" height="18" viewBox="0 0 212 18"><path d="M30 5l5 4-5 4z" fill="#fff"/><rect x="52" y="6" width="6" height="6" fill="#ccc"/><rect x="67" y="8" width="132" height="3" rx="1.5" fill="#555"/><rect x="67" y="8" width="62" height="3" rx="1.5" fill="#d22"/><path d="M199 5h4v4M203 5l-4 4" stroke="#ccc" fill="none"/></svg>
  </div>
</div>

<p class="enquiry abs">For Appointments or Enquiries please <b>call us on 1300 482 907</b> or <b>email:</b> &nbsp; <b>info@brambleridgepodiatry.net</b></p>

<section class="affiliations abs">
  <h2 class="abs">Our Affiliations</h2>
  <div class="badge abs" style="left:64px"><span></span></div>
  <div class="badge abs" style="left:231px"><span></span></div>
  <div class="badge abs" style="left:398px"><span></span></div>
  <div class="badge abs" style="left:565px"><span></span></div>
</section>

<section class="eligibility abs">
  <p class="abs">We are eligible service providers for all Veterans Gold Card holders. Transport &amp; workplace claims accepted. On the spot health insurance</p>
  <div class="book-orange abs">
    <svg width="12" height="12" viewBox="0 0 12 12" fill="none" stroke="#fff" stroke-width="1"><rect x="1" y="2" width="9" height="9"/><line x1="1" y1="4.5" x2="10" y2="4.5"/></svg>
    Book An Appointment
  </div>
</section>

<footer class="footer">
  <h3 class="abs" style="left:63px;width:78px">Quick Links</h3>
  <ul class="quick-links abs">
    <li>Consulting</li><li>Inspections</li><li>Training</li><li>General Contracing</li><li>Clients</li><li>Contact Us</li>
  </ul>
  <div class="col-divider abs" style="left:176px"></div>

  <h3 class="abs" style="left:205px;width:160px">Contact Details</h3>
  <div class="contact-list abs">
    <div class="contact-item"><svg width="8" height="10" viewBox="0 0 8 10"><path d="M4 10S0 5.5 0 4a4 4 0 018 0c0 1.5-4 6-4 6z" fill="#333"/><circle cx="4" cy="4" r="1.4" fill="#fff"/></svg><span>Suite 214 / 62 Larkfield<br>Street Melbourne 3000</span></div>
    <div class="contact-item"><svg width="9" height="9" viewBox="0 0 9 9"><path d="M1 1l2-0.5 1 2-1 1c.5 1.2 1.3 2 2.5 2.5l1-1 2 1L8 8C4 8 1 5 1 1z" fill="#333"/></svg><span>1300 482 907</span></div>
    <div class="contact-item"><svg width="10" height="8" viewBox="0 0 10 8"><rect width="10" height="8" fill="#333"/><path d="M0 0l5 4 5-4" stroke="#fff" fill="none"/></svg><span>info@brambleridgepodiatry.net</span></div>
  </div>
  <div class="col-divider abs" style="left:397px"></div>

  <h3 class="abs" style="left:426px;width:102px">Hours of Operation</h3>
  <div class="hours abs">
    <div>Monday to Friday<br>10:00am to 07:00pm</div>
    <div>Saturday<br>10:00am to 05:00pm</div>
    <div>Sunday<br>By Appointment Only</div>
  </div>
  <div class="col-divider abs" style="left:558px"></div>

  <div class="footer-logo abs"><span class="brand-dot"></span>Bramble Ridge Podiatry</div>
</footer>

<div class="bottom-bar abs">
  <p class="abs">Copyright © 2016 Northgate Web Services. &nbsp;All Right Reserved.</p>
  <span class="social abs" style="left:616px"></span>
  <span class="social abs" style="left:642px"></span>
  <span class="social abs" style="left:668px"></span>
</div>

</body>
</html>
```